RWT Fittings Ltd Business Cards

We need a business card with our business logo. We provide window and door installations on high-rises in west coast British Colombia, Canada.

I would like my business information and details on one side of the card, and the other side the company name with logo

Target Market(s)

General Contractors

Industry/Entity Type

Construction

Contact Information for Business Card

one side i want my company name and logo in the dark theme logo that i provided

Requirements
Must have
• Marco Peltieri, 16045518293, RWTFittings@mailbox-demo.com, 1407-5194 Linden Row Burnaby BC, V5H 2K9, Owner & Manager

```html
<!DOCTYPE html>
<html lang="en">
<head>
<meta charset="utf-8">
<title>RWT Fittings Ltd – Business Cards</title>
<link href="https://fonts.googleapis.com/css2?family=Open+Sans:wght@400;600;700;800&display=swap" rel="stylesheet">
<style>
  :root {
    --bg: #222222;
    --card-white: #ffffff;
    --brand-blue: #29a8e0;
    --brand-grey: #8c8c8c;
    --back-grey: #8a8a8a;
    --back-grey-dark: #7a7a7a;
    --ink: #111111;
    --rule: #222222;
  }
  * { box-sizing: border-box; margin: 0; padding: 0; }
  html, body { width: 1200px; height: 780px; overflow: hidden; background: var(--bg); }
  body { font-family: "Open Sans", Arial, sans-serif; position: relative; }

  .card {
    position: absolute;
    top: 236px;
    width: 540px;
    height: 308px;
    overflow: hidden;
  }
  .card--front { left: 40px; background: var(--card-white); }
  .card--back  { left: 620px; background: var(--back-grey); }

  /* Front */
  .brand {
    position: absolute;
    left: 28px;
    top: 74px;
    display: flex;
    align-items: center;
    gap: 10px;
  }
  .brand__square { width: 30px; height: 30px; background: var(--brand-grey); flex: none; }
  .brand__name {
    font-weight: 800;
    font-size: 22px;
    color: var(--brand-blue);
    white-space: nowrap;
  }
  .divider {
    position: absolute;
    left: 0; top: 0;
  }
  .contact {
    position: absolute;
    left: 298px;
    top: 54px;
  }
  .contact__name {
    font-weight: 800;
    font-size: 26px;
    color: var(--brand-blue);
    line-height: 1.1;
    white-space: nowrap;
  }
  .contact__title {
    font-weight: 600;
    font-size: 13px;
    color: var(--ink);
    margin-top: 2px;
  }
  .contact__list { list-style: none; margin-top: 12px; }
  .contact__item {
    display: flex;
    align-items: center;
    gap: 7px;
    font-size: 13px;
    color: var(--ink);
    line-height: 1.5;
    white-space: nowrap;
  }
  .contact__icon { width: 12px; height: 12px; flex: none; }

  .address-band {
    position: absolute;
    left: 0;
    bottom: 34px;
    width: 430px;
    height: 30px;
    background: var(--brand-blue);
    color: var(--card-white);
    font-size: 14px;
    line-height: 30px;
    padding-left: 36px;
    white-space: nowrap;
  }
  .corner-mark {
    position: absolute;
    right: 52px;
    bottom: 40px;
    width: 30px;
    height: 30px;
    background: var(--brand-blue);
  }
  .corner-block {
    position: absolute;
    right: 0;
    bottom: 0;
    width: 80px;
    height: 36px;
    background: var(--back-grey);
  }

  /* Back */
  .back-pattern {
    position: absolute;
    inset: 0;
    background: linear-gradient(135deg, var(--back-grey) 0%, var(--back-grey-dark) 100%);
  }
  .back-brand {
    position: absolute;
    right: 150px;
    bottom: 60px;
    display: flex;
    align-items: center;
    gap: 6px;
  }
  .back-brand__square { width: 12px; height: 12px; background: var(--card-white); }
  .back-brand__name {
    font-weight: 800;
    font-size: 13px;
    color: var(--card-white);
  }
</style>
</head>
<body>

<section class="card card--front" aria-label="Card front">
  <div class="brand">
    <span class="brand__square"></span>
    <span class="brand__name">RWT Fittings Ltd</span>
  </div>

  <svg class="divider" width="540" height="308" aria-hidden="true">
    <line x1="284" y1="44" x2="274" y2="222" stroke="var(--rule)" stroke-width="1"/>
  </svg>

  <div class="contact">
    <div class="contact__name">Marco Peltieri</div>
    <div class="contact__title">Owner &amp; Manager</div>
    <ul class="contact__list">
      <li class="contact__item">
        <svg class="contact__icon" viewBox="0 0 12 12" aria-hidden="true"><path d="M2.5 1 L4.5 1 L5 3.5 L3.8 4.4 Q4.8 6.8 7.6 8.2 L8.5 7 L11 7.5 L11 9.5 Q10.5 11 9 11 Q1 10 1 3 Q1 1.5 2.5 1Z" fill="var(--brand-blue)"/></svg>
        +1 (604) 551-8293
      </li>
      <li class="contact__item">
        <svg class="contact__icon" viewBox="0 0 12 12" aria-hidden="true"><rect x="0.5" y="2" width="11" height="8" rx="1" fill="var(--brand-blue)"/><path d="M1 2.5 L6 6.5 L11 2.5" stroke="#fff" stroke-width="1" fill="none"/></svg>
        RWTFittings@mailbox-demo.com
      </li>
      <li class="contact__item">
        <svg class="contact__icon" viewBox="0 0 12 12" aria-hidden="true"><circle cx="6" cy="6" r="5.5" fill="var(--brand-blue)"/><path d="M0.5 6 H11.5 M6 0.5 Q2.5 6 6 11.5 M6 0.5 Q9.5 6 6 11.5" stroke="#fff" stroke-width="0.8" fill="none"/></svg>
        www.rwtfittings-demo.com
      </li>
    </ul>
  </div>

  <div class="address-band">1407-5194 Linden Row Burnaby BC, V5H 2K9</div>
  <span class="corner-mark"></span>
  <span class="corner-block"></span>
</section>

<section class="card card--back" aria-label="Card back">
  <div class="back-pattern" role="img" aria-label="Repeating pattern of the company emblem in light grey"></div>
  <div class="back-brand">
    <span class="back-brand__square"></span>
    <span class="back-brand__name">RWT Fittings Ltd</span>
  </div>
</section>

</body>
</html>
```